Brightwell Aero Services Logo

I need a website and logo for the parent company Brightwell Aero Services, which encompasses general aviation aircraft repair, small aircrat rental and flight school. The company is based in Corvane, Ohio at the Tolleson county airport. A saying that can be incorporated somehere could be, "Quality flying is safe flying", "Safety in mind is no accident" ,. I need a website and logo.

The company started as a repair shop performing repairs and inspections on Harlan, Vantor, Delkin and Ralstead general aviation aircraft, all models of single engine piston, multi engine piston, and single engine turboprop with an emphasis on Harlan Solvane and AeroTurn turbo prop aircraft. We have se=ince entered the aircraft rental and flight instruction market using the Delkin 240 ang Harlan Ranger aircraft.

Number of Pages; I don't know. Maybe 5 ? A home page for Brightwell Aero Services, page for maintenance and repairs and a couple for the rental and school. The maintenance shop is busy, always has been. I need to get the rental and school advertised and busy.

I have a logo for the maintenance shop shirts, not for the school. I do not have the file. I paid a business locally to do that and print on the shirts. They have the file.

Target Market(s)

In our flight school rental fleet department, we are looking for persons wishing to obtain their private pilot license and continuing on into their commercial and instrument ratings. In the aircraft maintenance department, we are looking for new customers who want a better and more quality relationship with their aircraft maintenance provider who will give more detail and quality in the repairs with an emphasis on safety and fewer problems between scheduled maintenance cycles on their aircraft. Brightwell's owner, Dale Hutchins, has been performing aircraft maintenance in the Atlanta area for 27 years. He has built a steady customer base through those years.

```html
<!DOCTYPE html>
<html lang="en">
<head>
<meta charset="utf-8">
<title>Brightwell Aero Services</title>
<link href="https://fonts.googleapis.com/css2?family=Abel&family=Mulish:wght@400;600&display=swap" rel="stylesheet">
<style>
:root{
  --navy:#1b4b7c;
  --teal:#2596b8;
  --ice:#e4f1f6;
  --ink:#2b2b2b;
  --body:#4a4a4a;
  --white:#ffffff;
  --footer:#2398bf;
}
*{margin:0;padding:0;box-sizing:border-box}
html,body{width:1200px;height:3839px;overflow:hidden;background:var(--white)}
body{position:relative;font-family:"Mulish",sans-serif;color:var(--body)}
.abs{position:absolute}
.btn{position:absolute;background:var(--teal);color:var(--white);font-family:"Abel",sans-serif;font-size:14px;letter-spacing:.5px;display:flex;align-items:center;justify-content:center;text-transform:uppercase}
.photo{position:absolute}

/* header */
.brand{position:absolute;display:flex;align-items:center;gap:10px}
.brand-mark{width:26px;height:26px;border-radius:50%;background:var(--navy)}
.brand-name{font-family:"Abel",sans-serif;color:var(--navy);font-size:25px;line-height:1}
.main-nav{position:absolute;top:32px;right:160px;display:flex;gap:29px;font-family:"Abel",sans-serif;font-size:13px;color:var(--ink);text-transform:uppercase}
.main-nav .active{color:var(--teal)}

/* hero */
.hero-photo{left:496px;top:80px;width:704px;height:574px;background:linear-gradient(160deg,#5e6a6c 0%,#8c9497 40%,#c9cdcd 62%,#6b6a60 100%)}
.hero-panel{left:496px;top:161px;width:74px;height:408px;background:var(--white)}
.hero-kicker{left:161px;top:228px;font-size:55px;color:var(--ink);font-family:"Abel",sans-serif}
.hero-title{left:157px;top:282px;font-size:92px;color:var(--ink);font-family:"Abel",sans-serif;letter-spacing:-1px}
.hero-sub{left:162px;top:390px;font-size:33px;color:var(--ink);font-family:"Abel",sans-serif}

/* section titles */
.section-title{position:absolute;left:0;width:1200px;text-align:center;font-family:"Abel",sans-serif;font-weight:400;color:var(--navy);font-size:34px;text-transform:uppercase}
.rule{position:absolute;left:576px;width:48px;height:2px;background:var(--teal)}
.about-copy{left:246px;width:708px;text-align:center;font-size:13px;line-height:23px}

/* services */
.services-band{left:0;top:1072px;width:1200px;height:1428px;background:var(--ice)}
.service-card{position:absolute;background:var(--white);box-shadow:0 2px 10px rgba(0,0,0,.05);padding:34px 40px}
.service-card h3{font-family:"Abel",sans-serif;font-weight:400;color:var(--navy);font-size:26px;margin-bottom:14px}
.service-card p{font-size:12.5px;line-height:23px;margin-bottom:4px}
.checklist{list-style:none;font-size:12.5px;line-height:27px}
.checklist li{display:flex;align-items:center;gap:7px}

/* reviews */
.review-card{position:absolute;top:2719px;width:425px;height:206px;background:var(--white);box-shadow:0 2px 12px rgba(0,0,0,.06);text-align:center;padding:62px 20px 0}
.review-card .name{font-family:"Abel",sans-serif;color:var(--navy);font-size:19px;margin-bottom:6px}
.review-card p{font-size:12.5px;line-height:23px}
.review-bar{position:absolute;bottom:0;left:15px;right:15px;height:7px;background:#d3e8f0}
.avatar{position:absolute;top:-43px;left:169px;width:86px;height:86px;border-radius:50%;border:3px solid var(--teal);background:linear-gradient(180deg,#d8d2cc,#8a7b70)}
.arrow{position:absolute;top:2801px;width:42px;height:42px;border-radius:50%;display:flex;align-items:center;justify-content:center}

/* cta */
.cta{left:0;top:3017px;width:1200px;height:413px;background:linear-gradient(180deg,#3f6a9a,#355f8f 60%,#2f5987)}
.cta-title{left:0;top:3140px;width:1200px;text-align:center;font-family:"Abel",sans-serif;font-weight:400;color:var(--white);font-size:34px}
.cta-copy{left:210px;top:3190px;width:780px;text-align:center;color:#e6eef6;font-size:15.5px;line-height:28px}

/* footer */
.site-footer{left:0;top:3430px;width:1200px;height:409px;background:var(--footer)}
.footer-nav{position:absolute;top:3609px;left:0;width:1200px;display:flex;justify-content:center;gap:29px;font-family:"Abel",sans-serif;font-size:13px;color:var(--white);text-transform:uppercase}
.footer-rule{left:161px;top:3664px;width:878px;height:1px;background:rgba(255,255,255,.3)}
.contact-item{position:absolute;top:3697px;display:flex;gap:16px;align-items:center;font-size:13px;line-height:20px;color:var(--white)}
.contact-icon{width:42px;height:42px;background:var(--navy);display:flex;align-items:center;justify-content:center}
.contact-item b{font-weight:600}
.copyright{left:161px;top:3800px;font-size:12.5px;color:var(--white)}
.social{position:absolute;top:3801px;right:161px;display:flex;gap:18px}
.social span{width:16px;height:16px;border-radius:50%;background:var(--white)}
</style>
</head>
<body>

<header>
  <div class="brand" style="left:161px;top:30px">
    <span class="brand-mark"></span>
    <span class="brand-name">Brightwell Aero Services</span>
  </div>
  <nav class="main-nav">
    <span class="active">Home</span><span>Maintenance &amp; Repairs</span><span>Aircraft Rental</span><span>Flight School</span><span>Contact Us</span>
  </nav>
</header>

<section class="hero">
  <div class="photo hero-photo" role="img" aria-label="Aircraft hangar with small planes under maintenance"></div>
  <div class="abs hero-panel"></div>
  <div class="abs hero-kicker">Quality Flying is</div>
  <div class="abs hero-title">Safe Flying</div>
  <div class="abs hero-sub">Safety In Mind is No Accident</div>
  <div class="btn" style="left:161px;top:451px;width:139px;height:44px;font-size:15px">Contact Us</div>
</section>

<section class="about">
  <h2 class="section-title" style="top:730px">About Brightwell Aero Services</h2>
  <div class="rule" style="top:785px"></div>
  <p class="abs about-copy" style="top:802px">Lorem ipsum dolor sit amet, consectetur adipiscing elit, sed do eiusmod tempor incididunt ut labore et dolore magna aliqua. Ut enim ad minim veniam quis nostrud Lorem ipsum dolor sit amet.</p>
  <p class="abs about-copy" style="top:858px">Sed ut perspiciatis unde omnis iste natus error sit voluptatem accusantium doloremque laudantium, totam rem aperiam, eaque ipsa quae ab illo inventore veritatis et quasi architecto beatae vitae dicta sunt explicabo. Nemo enim ipsam voluptatem quia voluptas sit aspernatur aut odit aut fugit.</p>
  <div class="btn" style="left:545px;top:945px;width:108px;height:36px;font-size:13px">Contact Us</div>
</section>

<section class="services">
  <div class="abs services-band"></div>
  <h2 class="section-title" style="top:1153px">Our Services</h2>
  <div class="rule" style="top:1209px"></div>

  <div class="photo" style="left:161px;top:1249px;width:461px;height:350px;background:linear-gradient(135deg,#4a4c4e,#8f9294 50%,#c9c6c0 70%,#9a3a3a)" role="img" aria-label="Flight instructor and student inspecting a small plane"></div>
  <div class="service-card" style="left:599px;top:1279px;width:440px;height:289px">
    <h3>Flight School</h3>
    <p>Lorem ipsum dolor sit amet, consectetur adipiscing elit, sed do eiusmod tempor incididunt ut labore et dolore magna aliqua. Ut enim ad minim veniam quis nostrud.</p>
    <p>Quis autem vel eum iure reprehenderit qui in ea voluptate velit esse quam nihil molestiae consequatur...</p>
  </div>
  <div class="btn" style="left:638px;top:1493px;width:109px;height:36px;font-size:13px">Contact Us</div>

  <div class="photo" style="left:578px;top:1654px;width:461px;height:350px;background:linear-gradient(180deg,#e6dfe2 0%,#ddd6d8 55%,#8a8f6a 68%,#8e8a80 100%)" role="img" aria-label="Small single engine aircraft parked on a runway"></div>
  <div class="service-card" style="left:161px;top:1685px;width:439px;height:288px">
    <h3>Small Aircraft Rental</h3>
    <ul class="checklist">
      <li><svg width="12" height="12" viewBox="0 0 12 12"><rect x=".5" y=".5" width="11" height="11" fill="none" stroke="#2596b8"/><path d="M3 6l2 2 4-5" fill="none" stroke="#2596b8" stroke-width="1.6"/></svg>Lorem ipsum dolor sit amet consectetur adipiscing.</li>
      <li><svg width="12" height="12" viewBox="0 0 12 12"><rect x=".5" y=".5" width="11" height="11" fill="none" stroke="#2596b8"/><path d="M3 6l2 2 4-5" fill="none" stroke="#2596b8" stroke-width="1.6"/></svg>Ut enim ad minim veniam quis nostrud semper.</li>
      <li><svg width="12" height="12" viewBox="0 0 12 12"><rect x=".5" y=".5" width="11" height="11" fill="none" stroke="#2596b8"/><path d="M3 6l2 2 4-5" fill="none" stroke="#2596b8" stroke-width="1.6"/></svg>laboris nisi ut aliquip ex ea commodo consequat.</li>
      <li><svg width="12" height="12" viewBox="0 0 12 12"><rect x=".5" y=".5" width="11" height="11" fill="none" stroke="#2596b8"/><path d="M3 6l2 2 4-5" fill="none" stroke="#2596b8" stroke-width="1.6"/></svg>Duis aute irure dolor in reprehenderit involuptate.</li>
    </ul>
  </div>
  <div class="btn" style="left:201px;top:1891px;width:109px;height:36px;font-size:13px">Contact Us</div>

  <div class="photo" style="left:161px;top:2059px;width:461px;height:350px;background:linear-gradient(160deg,#5e6a6c 0%,#8c9497 40%,#c9cdcd 62%,#6b6a60 100%)" role="img" aria-label="Hangar interior with aircraft undergoing repair"></div>
  <div class="service-card" style="left:599px;top:2089px;width:440px;height:289px">
    <h3>Aircraft Repair</h3>
    <p>Lorem ipsum dolor sit amet, consectetur adipiscing elit, sed do eiusmod tempor incididunt ut labore et dolore magna aliqua. Ut enim ad minim veniam quis nostrud.</p>
    <p>Quis autem vel eum iure reprehenderit qui in ea voluptate velit esse quam nihil molestiae consequatur...</p>
  </div>
  <div class="btn" style="left:638px;top:2303px;width:109px;height:36px;font-size:13px">Contact Us</div>
</section>

<section class="reviews">
  <h2 class="section-title" style="top:2580px">Customer Reviews</h2>
  <div class="rule" style="top:2636px"></div>

  <div class="arrow" style="left:79px;border:1.5px solid var(--teal)">
    <svg width="12" height="14" viewBox="0 0 12 14"><path d="M8 2L3 7l5 5" fill="none" stroke="#2596b8" stroke-width="2.2"/></svg>
  </div>
  <div class="arrow" style="left:1077px;background:var(--teal)">
    <svg width="12" height="14" viewBox="0 0 12 14"><path d="M4 2l5 5-5 5" fill="none" stroke="#fff" stroke-width="2.2"/></svg>
  </div>

  <div class="review-card" style="left:161px">
    <div class="avatar" role="img" aria-label="Reviewer portrait"></div>
    <div class="name">Neil Ashby</div>
    <p>Lorem ipsum dolor sit amet, consectetur adipiscing elit, sed do eiusmod tempor incididunt ut labore et dolore magna aliqua. Ut enim ad minim veniam Nemo enim ipsam voluptatem quia voluptas sit aspernatur...</p>
    <div class="review-bar"></div>
  </div>
  <div class="review-card" style="left:614px">
    <div class="avatar" role="img" aria-label="Reviewer portrait"></div>
    <div class="name">Carla Wendt</div>
    <p>Lorem ipsum dolor sit amet, consectetur adipiscing elit, sed do eiusmod tempor incididunt ut labore et dolore magna aliqua. Ut enim ad minim veniam Nemo enim ipsam voluptatem quia voluptas sit aspernatur...</p>
    <div class="review-bar"></div>
  </div>
</section>

<section>
  <div class="abs cta" role="img" aria-label="Aerial view of the airport area under a blue tint"></div>
  <h2 class="abs cta-title">Lorem Ipsum Dolor Sit Amet Conse Ctetur</h2>
  <p class="abs cta-copy">At vero eos et accusamus et iusto odio dignissimos ducimus qui blanditiis praesentium voluptatum deleniti atque corrupti quos dolores et quas molestias excepturi sint.</p>
  <div class="btn" style="left:547px;top:3260px;width:107px;height:36px;font-size:13px">Contact Us</div>
</section>

<footer>
  <div class="abs site-footer"></div>
  <div class="brand" style="left:0;width:1200px;top:3520px;justify-content:center">
    <span class="brand-mark" style="background:var(--white)"></span>
    <span class="brand-name" style="color:var(--white);font-size:32px">Brightwell Aero Services</span>
  </div>
  <nav class="footer-nav"><span>Home</span><span>Maintenance &amp; Repairs</span><span>Aircraft Rental</span><span>Flight School</span><span>Contact Us</span></nav>
  <div class="abs footer-rule"></div>

  <div class="contact-item" style="left:240px">
    <div class="contact-icon"><svg width="16" height="20" viewBox="0 0 16 20"><path d="M8 1a6 6 0 0 0-6 6c0 5 6 12 6 12s6-7 6-12a6 6 0 0 0-6-6z" fill="#fff"/><circle cx="8" cy="7" r="2.3" fill="#1b4b7c"/></svg></div>
    <div>Lorem ipsum dolor sit<br>Corvane, Ohio</div>
  </div>
  <div class="contact-item" style="left:539px">
    <div class="contact-icon"><svg width="18" height="18" viewBox="0 0 18 18"><path d="M4 1l3 4-2 2c1 2 3 4 5 5l2-2 4 3-2 3C8 16 2 10 1 4z" fill="#fff"/></svg></div>
    <div><b>PHONE</b><br>123 456 7890</div>
  </div>
  <div class="contact-item" style="left:776px">
    <div class="contact-icon"><svg width="18" height="18" viewBox="0 0 18 18"><path d="M1 8l16-7-5 16-3-6z" fill="#fff"/></svg></div>
    <div><b>EMAIL</b><br>info@brightwellaero.com</div>
  </div>

  <div class="abs copyright">© 2022 Brightwell Aero Services. All Rights Reserved.</div>
  <div class="social"><span></span><span></span><span></span><span></span></div>
</footer>

</body>
</html>
```